"Harbor Builders" is a residential building company and needs a new business card design and may re

We would like a redesign based on the existing logo, and would like to see a new font as well. We are bespoke home builders who build sustainable energy efficient homes.

Industry/Entity Type

Construction

Contact Information for Business Card

Business card size 40mm x 90mm

Colors

Designer to choose colors to be used in the design.

```html
<!DOCTYPE html>
<html lang="en">
<head>
<meta charset="utf-8">
<title>Harbor Builders – Business Card</title>
<link href="https://fonts.googleapis.com/css2?family=Source+Sans+3:wght@400;600;700&display=swap" rel="stylesheet">
<style>
  :root {
    --backdrop: #8a8b8d;
    --card-light: #e4e4e6;
    --card-dark: #040506;
    --ink: #1d1d1f;
    --ink-soft: #3e3e42;
    --rule: #9a9a9e;
    --accent: #9cbc2a;
    --paper-white: #e8e8ea;
  }
  html, body {
    margin: 0;
    padding: 0;
    width: 1105px;
    height: 1200px;
    overflow: hidden;
    background: var(--backdrop);
    font-family: "Source Sans 3", "Myriad Pro", Arial, sans-serif;
  }
  .canvas { position: relative; width: 1105px; height: 1200px; }
  .card {
    position: absolute;
    left: 182px;
    width: 747px;
    height: 426px;
    box-sizing: border-box;
  }
  .card--front { top: 119px; background: var(--card-light); }
  .card--back { top: 636px; background: var(--card-dark); }

  .brand {
    position: absolute;
    display: flex;
    align-items: center;
    gap: 14px;
    font-weight: 600;
    white-space: nowrap;
  }
  .brand__square { display: block; background: var(--accent); }
  .card--front .brand { left: 62px; top: 188px; font-size: 34px; color: var(--ink); }
  .card--front .brand__square { width: 26px; height: 26px; }

  .divider {
    position: absolute;
    left: 362px; top: 112px;
    width: 1px; height: 206px;
    background: var(--rule);
  }
  .details { position: absolute; left: 398px; top: 100px; color: var(--ink-soft); }
  .details__name { margin: 0; font-size: 26px; font-weight: 700; color: var(--ink); line-height: 1.2; }
  .details__company { margin: 6px 0 0; font-size: 16px; font-weight: 700; line-height: 1.3; }
  .details__address { margin: 0; font-size: 17px; line-height: 1.3; }
  .contact { list-style: none; margin: 14px 0 0; padding: 0; font-size: 17px; }
  .contact li { display: flex; align-items: center; gap: 10px; height: 24px; }
  .contact svg { width: 16px; height: 16px; fill: var(--ink); flex: none; }
  .details__legal { margin: 12px 0 0; font-size: 15px; color: var(--ink); }
  .details__legal b { font-weight: 700; }

  .card--back .brand { left: 50%; top: 50%; transform: translate(-50%, -50%); font-size: 56px; color: var(--paper-white); gap: 20px; }
  .card--back .brand__square { width: 40px; height: 40px; }
</style>
</head>
<body>
<div class="canvas">
  <section class="card card--front" aria-label="Business card front">
    <div class="brand"><span class="brand__square"></span>Harbor Builders</div>
    <div class="divider"></div>
    <div class="details">
      <p class="details__name">Daniel Moretti</p>
      <p class="details__company">Harbor Builders Pty Ltd</p>
      <p class="details__address">PO Box 4820 Northgate<br>LPO Bayview WA 6091</p>
      <ul class="contact">
        <li><svg viewBox="0 0 16 16" aria-hidden="true"><path d="M4 0h8a1 1 0 0 1 1 1v14a1 1 0 0 1-1 1H4a1 1 0 0 1-1-1V1a1 1 0 0 1 1-1zm1 2v10h6V2zm3 11a1 1 0 1 0 0 2 1 1 0 0 0 0-2z"/></svg>0412 558 730</li>
        <li><svg viewBox="0 0 16 16" aria-hidden="true"><path d="M1 3h14v1.2L8 9 1 4.2zM1 5.8 8 10.6l7-4.8V13H1z"/></svg>daniel@harborbuilders.com.au</li>
        <li><svg viewBox="0 0 16 16" aria-hidden="true"><circle cx="8" cy="8" r="7"/><path d="M1 8h14M8 1c-3 3.5-3 10.5 0 14M8 1c3 3.5 3 10.5 0 14" stroke="#e4e4e6" stroke-width="1.2" fill="none"/></svg>www.harborbuilders.com.au</li>
      </ul>
      <p class="details__legal"><b>Registration:</b> 40318 &nbsp;<b>ABN</b>: 52 204 661 378</p>
    </div>
  </section>

  <section class="card card--back" aria-label="Business card back">
    <div class="brand"><span class="brand__square"></span>Harbor Builders</div>
  </section>
</div>
</body>
</html>
```